New iOS App design for Boston Startup

We are looking for a new app design for our iPhone app. The current app's design feels outdated and we like to add lots of new functionality and a new navigation as well. A complete overhaul therefore!
We want you to design 5 screens that will have changed the most. The complete wireframes of these 5 pages are attached in the requirements document.
Once the winning design is selected we will award the winner with the designing all other screens (40-50 screens based on the same design). This will be a separate project worth $1000. The winning designer can get more follow up work if both sides are happy about the cooperation.
We will give feedback as soon as the first screen has been uploaded for review. Final decision will be made only after all 5 screens are finished.
We hope you give it your best!
Note: will only communicate through PixelHarbor (no skype),
Updates
Reason: Want to give designers a chance to submit their designs as I understand from some, the deadline is too close.
I have raised the award and introduced a 2nd price as well to make it worth your time. I hope you give it your best shot.
Reason: A few of you have asked for an extension of the deadline as time is running out. I will extend by one day. Tell me if you need more.
Industry/Entity Type
Startup
Requirements
Must have
- At least 1 screen before we can give you feedback.
Nice to have
- multiple options of 1 screen to get to a desirable design

```html
<!DOCTYPE html>
<html lang="en">
<head>
<meta charset="utf-8">
<title>Study App – Home Screen</title>
<link rel="stylesheet" href="https://fonts.googleapis.com/css2?family=Open+Sans:wght@400;600;700&display=swap">
<style>
  :root {
    --canvas-bg: #ffffff;
    --brand-blue: #1f88d6;
    --brand-blue-dark: #1a74b8;
    --surface: #ffffff;
    --surface-muted: #ececec;
    --text-main: #3a3a3a;
    --text-soft: #6f6f6f;
    --positive: #7cc21f;
    --negative: #e8323a;
    --button-dark: #555555;
    --divider: #dcdcdc;
  }
  * { box-sizing: border-box; margin: 0; padding: 0; }
  html, body {
    width: 1200px; height: 1041px; overflow: hidden;
    background: var(--canvas-bg);
    font-family: "Open Sans", Helvetica, Arial, sans-serif;
    color: var(--text-main);
  }
  .canvas {
    width: 1200px; height: 1041px;
    display: flex; align-items: center; justify-content: center;
  }
  .app-screen {
    width: 450px; height: 800px;
    background: var(--surface);
    display: flex; flex-direction: column;
    border: 1px solid var(--divider);
    overflow: hidden;
  }

  /* Header */
  .app-header { background: var(--brand-blue); color: #fff; }
  .status-bar {
    height: 24px; padding: 0 10px;
    display: flex; align-items: center; justify-content: space-between;
    font-size: 11px; font-weight: 600;
  }
  .status-bar .carrier { display: flex; align-items: center; gap: 6px; }
  .status-bar .signal { letter-spacing: 1px; font-size: 14px; line-height: 1; }
  .status-bar .power { display: flex; align-items: center; gap: 6px; }
  .battery { width: 24px; height: 11px; border: 1px solid #fff; border-radius: 2px; padding: 1px; }
  .battery span { display: block; height: 100%; background: #fff; border-radius: 1px; }
  .title-bar {
    height: 50px; display: flex; align-items: center; padding: 0 14px;
    position: relative;
  }
  .title-bar h1 {
    position: absolute; left: 0; right: 0; text-align: center;
    font-size: 19px; font-weight: 600;
  }

  /* Score */
  .score-panel {
    padding: 22px 20px 8px;
    display: flex; align-items: baseline; justify-content: center; gap: 14px;
  }
  .score-label { font-size: 30px; color: var(--text-soft); }
  .score-value { font-size: 76px; font-weight: 700; color: var(--brand-blue); line-height: 1; letter-spacing: -1px; }
  .score-delta { font-size: 26px; color: var(--negative); }

  /* Stats carousel */
  .stats-row {
    display: flex; align-items: center; padding: 6px 4px 16px;
  }
  .stats-arrow { width: 18px; height: 18px; flex: none; }
  .stats-track { flex: 1; display: flex; justify-content: space-between; white-space: nowrap; }
  .stat { flex: none; width: 100px; text-align: center; }
  .stat-figure { font-size: 14px; font-weight: 700; color: var(--positive); }
  .stat-figure .delta { color: var(--text-main); font-weight: 600; margin-left: 3px; }
  .stat-caption { font-size: 14px; color: var(--text-soft); }

  /* Tiles */
  .tile-grid { display: grid; grid-template-columns: repeat(3, 1fr); gap: 2px; background: #fff; }
  .tile {
    background: var(--brand-blue); color: #fff; height: 140px;
    display: flex; flex-direction: column; align-items: center; justify-content: center;
    position: relative; text-align: center; font-size: 16px; line-height: 1.25;
    padding: 0 28px;
  }
  .tile svg.tile-icon { width: 34px; height: 30px; margin-bottom: 10px; }
  .tile .chevron { position: absolute; right: 10px; top: 50%; width: 10px; height: 14px; transform: translateY(-50%); }

  /* Up next */
  .up-next {
    flex: 1; background: var(--surface-muted);
    display: flex; flex-direction: column; align-items: center; padding-top: 34px;
  }
  .up-next h2 { font-size: 17px; font-weight: 700; margin-bottom: 12px; }
  .up-next-button {
    width: 400px; height: 56px; border-radius: 6px;
    background: var(--button-dark); color: #fff;
    display: flex; align-items: center; justify-content: center;
    font-size: 20px;
  }

  /* Tab bar */
  .tab-bar {
    height: 72px; display: flex; background: var(--surface);
    border-top: 1px solid var(--divider);
  }
  .tab {
    flex: 1; display: flex; flex-direction: column; align-items: center; justify-content: center;
    gap: 4px; font-size: 11px; font-weight: 600; color: var(--text-soft);
  }
  .tab svg { width: 30px; height: 26px; }
  .tab.is-active { color: var(--brand-blue-dark); }
</style>
</head>
<body>
<main class="canvas">
  <section class="app-screen">
    <header class="app-header">
      <div class="status-bar">
        <div class="carrier"><span class="signal">•••</span><span>NOVA</span>
          <svg width="12" height="10" viewBox="0 0 12 10"><path d="M1 4a7 7 0 0 1 10 0M3 6a4 4 0 0 1 6 0" stroke="#fff" stroke-width="1.4" fill="none"/><circle cx="6" cy="8.5" r="1.1" fill="#fff"/></svg>
        </div>
        <span class="clock">4:21 PM</span>
        <div class="power">
          <svg width="7" height="11" viewBox="0 0 7 11"><path d="M1 3l5 5-2.5 2V1L6 3 1 8" stroke="#fff" stroke-width="1" fill="none"/></svg>
          <span>100%</span><div class="battery"><span></span></div>
        </div>
      </div>
      <div class="title-bar">
        <svg width="26" height="18" viewBox="0 0 26 18"><path d="M0 2h26M0 9h26M0 16h26" stroke="#fff" stroke-width="2.6"/></svg>
        <h1>Welcome back, Noam</h1>
      </div>
    </header>

    <div class="score-panel">
      <span class="score-label">Score</span>
      <span class="score-value">650</span>
      <span class="score-delta">-18</span>
    </div>

    <div class="stats-row">
      <svg class="stats-arrow" viewBox="0 0 18 18"><path d="M11 3L5 9l6 6" stroke="#9a9a9a" stroke-width="2" fill="none"/></svg>
      <div class="stats-track">
        <div class="stat"><div class="stat-figure">34%<span class="delta">+4</span></div><div class="stat-caption">Completion</div></div>
        <div class="stat"><div class="stat-figure">20<span class="delta">+3</span></div><div class="stat-caption">Sessions</div></div>
        <div class="stat"><div class="stat-figure">18<span class="delta">+10</span></div><div class="stat-caption">Sessions</div></div>
        <div class="stat"><div class="stat-figure">&nbsp;</div><div class="stat-caption">This week</div></div>
      </div>
      <svg class="stats-arrow" viewBox="0 0 18 18"><path d="M7 3l6 6-6 6" stroke="#9a9a9a" stroke-width="2" fill="none"/></svg>
    </div>

    <nav class="tile-grid">
      <a class="tile">
        <svg class="tile-icon" viewBox="0 0 34 30"><path d="M3 27h28M7 26V18M12 26V14M17 26V16M22 26V10M27 26V6" stroke="#fff" stroke-width="2.4" fill="none"/><path d="M5 14l8-6 6 4 10-9" stroke="#fff" stroke-width="1.6" fill="none"/></svg>
        Analytics
        <svg class="chevron" viewBox="0 0 10 14"><path d="M2 1l6 6-6 6" stroke="#fff" stroke-width="2" fill="none"/></svg>
      </a>
      <a class="tile">
        <svg class="tile-icon" viewBox="0 0 34 30"><path d="M4 5h11a2 2 0 0 1 2 2v19a2 2 0 0 0-2-2H4zM30 5H19a2 2 0 0 0-2 2v19a2 2 0 0 1 2-2h11z" stroke="#fff" stroke-width="1.8" fill="none"/></svg>
        Course Overview
        <svg class="chevron" viewBox="0 0 10 14"><path d="M2 1l6 6-6 6" stroke="#fff" stroke-width="2" fill="none"/></svg>
      </a>
      <a class="tile">
        <svg class="tile-icon" viewBox="0 0 34 30"><rect x="4" y="5" width="22" height="20" rx="2" stroke="#fff" stroke-width="1.8" fill="none"/><path d="M4 11h22M10 2v6M20 2v6" stroke="#fff" stroke-width="1.8"/><circle cx="25" cy="22" r="6" fill="var(--brand-blue)" stroke="#fff" stroke-width="1.8"/><path d="M25 19v3.5h2.5" stroke="#fff" stroke-width="1.5" fill="none"/></svg>
        Days Until Test 33
        <svg class="chevron" viewBox="0 0 10 14"><path d="M2 1l6 6-6 6" stroke="#fff" stroke-width="2" fill="none"/></svg>
      </a>
    </nav>

    <section class="up-next">
      <h2>Up Next:</h2>
      <a class="up-next-button">Sentence Correction Lesson 4</a>
    </section>

    <footer class="tab-bar">
      <a class="tab">
        <svg viewBox="0 0 30 26"><path d="M3 13L15 3l12 10" stroke="#777" stroke-width="2.2" fill="none"/><path d="M7 12v11h6v-6h4v6h6V12" fill="#777"/></svg>Home
      </a>
      <a class="tab">
        <svg viewBox="0 0 30 26"><path d="M3 5h10a2 2 0 0 1 2 2v16a2 2 0 0 0-2-2H3zM27 5H17a2 2 0 0 0-2 2v16a2 2 0 0 1 2-2h10z" stroke="#777" stroke-width="1.8" fill="none"/></svg>Theory
      </a>
      <a class="tab is-active">
        <svg viewBox="0 0 30 26"><rect x="2" y="10" width="8" height="12" fill="#1a74b8"/><rect x="11" y="7" width="8" height="12" fill="#1a74b8"/><rect x="20" y="4" width="8" height="12" fill="#1a74b8"/></svg>Practice
      </a>
      <a class="tab">
        <svg viewBox="0 0 30 26"><path d="M8 7h14a6 6 0 0 1 6 7l-1 5a3 3 0 0 1-5 1l-3-3h-8l-3 3a3 3 0 0 1-5-1l-1-5a6 6 0 0 1 6-7z" fill="#777"/><path d="M9 11v5M6.5 13.5h5" stroke="#fff" stroke-width="1.6"/><circle cx="20" cy="12" r="1.3" fill="#fff"/><circle cx="23" cy="15" r="1.3" fill="#fff"/></svg>Games
      </a>
      <a class="tab">
        <svg viewBox="0 0 30 26"><circle cx="15" cy="13" r="11" fill="#777"/><path d="M10 13l4 4 7-8" stroke="#fff" stroke-width="2.4" fill="none"/></svg>Test
      </a>
    </footer>
  </section>
</main>
</body>
</html>
```